Electrictrian Contractor Website Design

We are working with an electrical contractor in California called Fennick Electric.

Some sites to use for content/competitors and inspiration:
https://corvanelectric.example
https://tralvenpage.example/web/contractor/ (lots of contractor website designs we've approved and continue to show clients)

Thank you for taking the time to consider designing a website for us. We are web developers based in Stockton, CA, USA. Most of our projects go through the same process. Understanding this process may help you win a project with us. We custom-code all of our websites in-house. We don’t have any requirements as to what tools you use for your design, but we prefer Figma files. For any design that we label as four-stars, we send it to the client for review. The client picks the final design they want us to use. Once we complete this process, we will continue to show additional clients all the four-star sites and purchase them later. Your designs will have multiple chances to sell. For better chances of success, we ask that you follow these guidelines.

IMAGES:
If you use any images or icons in the design, we ask that you have a link to the asset so we can purchase the image/icon. Most of the designs we submit do not have the customer’s images on them unless they have some great images. Be creative; show us the feeling you are trying to portray with your image choices. Use any royalty-free site you choose. We subscribe to Quorvane and mainly use their images, but we can purchase images outside of Quorvane.

PLEASE NOTE: we will not submit designs to clients with watermarks on the images.

FONTS:
We ask that you identify the fonts used in the design. This can be done in a message if you want. We typically use Pellmarsh Type and Quorvane Type.

CONTENT:
We're always open to different content and ideas. We often submit designs with stock images so the client can see our vision. We typically take pictures after the website launch to use their images with our vision. Lorem Ipsum is fine for paragraphs, but we ask that you write the headers in correct English. We want to be able to show the vision and identify the sections of the website.

INSPIRATION:
We typically add a couple of links in the brief of websites we like to help you get started in your design.

REVISIONS:
We do not often ask for revisions of the designs unless we see something in the design that may not appeal to the client. If there are slight changes that we want to make, we do that in the development process.

FEEDBACK:
We rarely give feedback on designs during the design process. We are working on many website projects and do not have the time to provide feedback. We usually respond if your request is well thought out and asks specific questions, but a note asking “feedback, please” usually goes unanswered

```html
<!DOCTYPE html>
<html lang="en">
<head>
<meta charset="utf-8">
<title>Fennick Electric</title>
<link href="https://fonts.googleapis.com/css2?family=Outfit:wght@400;500;600;700&family=Roboto:wght@400;500;700&display=swap" rel="stylesheet">
<style>
:root{
  --blue:#0b4490;
  --blue-deep:#08356f;
  --yellow:#f7b500;
  --white:#ffffff;
  --ink:#3b3b3b;
  --muted:#5a5a5a;
  --light:#f3f3f3;
  --head:'Outfit',sans-serif;
  --body:'Roboto',sans-serif;
}
*{box-sizing:border-box;margin:0;padding:0}
html,body{width:1200px;height:4695px;overflow:hidden}
body{position:relative;background:var(--white);font-family:var(--body);color:var(--ink)}
.abs{position:absolute}
.band{position:absolute;left:0;width:1200px}
a{text-decoration:none;color:inherit}

/* header */
.site-header{top:0;height:128px;background:var(--white)}
.socials{display:flex;gap:9px;position:absolute}
.social-dot{width:33px;height:33px;border-radius:50%;border:1.5px solid var(--blue);display:flex;align-items:center;justify-content:center}
.social-dot::after{content:"";width:9px;height:9px;border-radius:50%;background:var(--blue)}
.social-dot.active{background:var(--yellow);border-color:var(--yellow)}
.social-dot.active::after{background:var(--white)}
.header-socials{left:111px;top:50px}
.logo{position:absolute;text-align:center;font-family:var(--head);font-weight:500;color:var(--blue);line-height:1}
.logo span{display:block}
.logo .top{letter-spacing:10px;font-weight:600}
.logo .bottom{letter-spacing:9px}
.header-logo{left:430px;width:340px;top:28px;font-size:36px}
.header-logo span+span{margin-top:6px}
.call{position:absolute;left:850px;top:42px;display:flex;align-items:center;gap:14px}
.call-icon{width:50px;height:50px;border-radius:50%;background:var(--white);box-shadow:0 3px 12px rgba(0,0,0,.14);display:flex;align-items:center;justify-content:center}
.call small{display:block;font-size:10px;font-weight:500;color:var(--ink)}
.call strong{display:block;font-size:20px;font-weight:500;color:var(--blue);margin-top:3px}

.main-nav{top:128px;height:51px;background:var(--blue);display:flex;justify-content:center;align-items:center;gap:47px;padding-right:20px}
.main-nav a{font-size:15px;font-weight:500;color:var(--white)}
.main-nav a.current{color:var(--yellow)}

/* hero */
.hero{top:179px;height:640px;background:
  radial-gradient(ellipse 380px 300px at 820px 150px,rgba(214,150,80,.75),rgba(214,150,80,0) 70%),
  radial-gradient(ellipse 300px 260px at 1080px 80px,rgba(120,90,60,.8),rgba(120,90,60,0) 70%),
  radial-gradient(ellipse 360px 320px at 200px 250px,rgba(110,130,140,.55),rgba(110,130,140,0) 70%),
  radial-gradient(ellipse 260px 200px at 560px 420px,rgba(60,55,40,.7),rgba(60,55,40,0) 70%),
  linear-gradient(100deg,#1d2a33 0%,#35444d 30%,#4a3e33 55%,#6e5238 75%,#2e231b 100%)}
.hero::after{content:"";position:absolute;inset:0;background:rgba(10,15,20,.22)}
.hero-copy{position:absolute;z-index:1;left:0;width:1200px;top:190px;text-align:center;color:var(--white)}
.hero-copy .kicker{font-family:var(--head);font-size:24px;font-weight:400}
.hero-copy h1{font-family:var(--head);font-size:48px;font-weight:500;margin-top:4px;line-height:1.1}
.hero-copy p{font-size:19px;line-height:30px;margin:12px auto 0;width:520px}
.btn-solid{display:inline-block;background:var(--yellow);color:var(--white);font-size:13px;font-weight:700;border-radius:24px;width:146px;height:44px;line-height:44px;margin-top:22px}
.slider-dots{position:absolute;z-index:1;left:1143px;top:254px;display:flex;flex-direction:column;align-items:center;gap:18px}
.slider-dots i{display:block;width:7px;height:7px;border-radius:50%;background:var(--white)}
.slider-dots i.on{width:10px;height:10px;box-shadow:0 0 0 6px rgba(255,255,255,.35)}

/* about */
.about{top:819px;height:662px;background:var(--blue)}
.about-text{position:absolute;left:638px;top:140px;width:450px;color:var(--white)}
.section-title{font-family:var(--head);font-weight:600;font-size:40px;line-height:1.15;text-transform:uppercase}
.section-title .hl{color:var(--yellow)}
.about-text p{font-size:15.3px;line-height:27px;text-align:justify;margin-top:18px}
.about-text p+p{margin-top:10px}
.btn-outline{display:inline-block;border:2px solid var(--yellow);border-radius:26px;color:var(--white);font-size:13px;font-weight:700;width:140px;height:46px;line-height:42px;text-align:center;margin-top:34px}

/* services */
.services{top:1481px;height:755px;background:var(--white)}
.center-title{position:absolute;left:0;width:1200px;text-align:center;color:var(--blue)}
.service-card{position:absolute;top:179px;width:305px;height:465px;background:var(--white);border-radius:18px;box-shadow:0 4px 14px rgba(0,0,0,.16);text-align:center}
.service-card.featured{border:2px solid var(--yellow)}
.service-card .photo{position:absolute;left:8px;top:8px;right:8px;height:213px;border-radius:14px}
.service-card h3{position:absolute;top:250px;left:0;right:0;font-size:18px;font-weight:500;line-height:26px;color:var(--blue);text-transform:uppercase}
.service-card p{position:absolute;top:306px;left:26px;right:26px;font-size:15px;line-height:26px;color:var(--muted)}
.read-more{color:var(--yellow);font-weight:700;text-decoration:underline}
.service-card .read-more{position:absolute;top:418px;left:0;right:0;font-size:13px}
.arrow-btn{position:absolute;top:396px;width:34px;height:34px;border-radius:50%;display:flex;align-items:center;justify-content:center}
.arrow-btn.prev{left:38px;background:#eef2f8;box-shadow:0 2px 6px rgba(0,0,0,.12)}
.arrow-btn.next{left:1127px;background:var(--yellow)}

/* commercial */
.commercial{top:2236px;height:533px;background:
  radial-gradient(ellipse 300px 260px at 150px 80px,rgba(70,110,170,.5),rgba(70,110,170,0) 70%),
  radial-gradient(ellipse 320px 260px at 480px 460px,rgba(60,100,160,.45),rgba(60,100,160,0) 70%),
  linear-gradient(100deg,#0b4490 0%,#0e4a96 50%,#1a5298 100%)}
.commercial-text{position:absolute;left:111px;top:92px;width:434px;color:var(--white)}
.commercial-text p{font-size:15px;line-height:26.6px;text-align:justify;margin-top:22px}
.commercial-photo{position:absolute;left:600px;top:79px;width:489px;height:377px;border-radius:14px;background:
  radial-gradient(ellipse 180px 220px at 110px 180px,rgba(230,190,110,.85),rgba(230,190,110,0) 70%),
  radial-gradient(ellipse 160px 120px at 380px 90px,rgba(235,235,230,.9),rgba(235,235,230,0) 70%),
  radial-gradient(ellipse 200px 160px at 340px 280px,rgba(200,200,60,.75),rgba(200,200,60,0) 70%),
  linear-gradient(120deg,#6a6457 0%,#8a7a52 40%,#4e5036 70%,#2e3440 100%)}

/* gallery */
.gallery{top:2769px;height:870px;background:var(--white)}
.tile{position:absolute;border-radius:12px}

/* blog */
.blog{top:3639px;height:660px;background:var(--light)}
.blog-photo{position:absolute}
.blog-card{position:absolute;left:157px;top:401px;width:399px;height:160px;background:var(--white);padding:52px 30px 0 30px}
.date-pill{position:absolute;background:var(--yellow);color:var(--white);font-size:11px;font-weight:500;border-radius:20px;width:120px;height:38px;line-height:38px;text-align:center}
.blog-card .date-pill{left:27px;top:-13px}
.blog-card h4,.blog-item h4{font-size:15px;font-weight:500;line-height:22px;color:var(--blue);text-transform:uppercase}
.blog-card p,.blog-item p{font-size:13px;line-height:21px;color:#333;margin-top:6px}
.blog-item{position:absolute;left:846px;width:260px}
.blog-item .date-pill{position:static;display:block;margin-bottom:13px}

/* footer */
.site-footer{top:4277px;height:418px;background:var(--blue)}
.footer-logo{left:430px;width:340px;top:114px;font-size:36px;color:var(--white)}
.footer-logo span+span{margin-top:6px}
.footer-nav{position:absolute;left:0;width:1200px;top:212px;display:flex;justify-content:center;gap:26px;color:var(--white);font-size:16px;font-weight:500}
.footer-contact{position:absolute;left:0;width:1200px;top:252px;display:flex;justify-content:center;align-items:center;gap:14px;color:var(--white);font-size:13px}
.footer-contact span{display:flex;align-items:center;gap:7px}
.footer-socials{left:530px;top:289px}
.footer-socials .social-dot{width:30px;height:30px;border-color:var(--white)}
.footer-socials .social-dot::after{background:var(--white);width:8px;height:8px}
.footer-socials .social-dot.active{border-color:var(--yellow)}
.footer-rule{position:absolute;left:111px;width:978px;top:349px;height:1px;background:rgba(255,255,255,.25)}
.copyright{position:absolute;left:0;width:1200px;top:370px;text-align:center;color:var(--white);font-size:11px}
</style>
</head>
<body>

<header class="band site-header">
  <div class="socials header-socials" aria-label="Social links">
    <span class="social-dot active"></span>
    <span class="social-dot"></span>
    <span class="social-dot"></span>
    <span class="social-dot"></span>
  </div>
  <div class="logo header-logo"><span class="top">FENNICK</span><span class="bottom">ELECTRIC</span></div>
  <div class="call">
    <div class="call-icon">
      <svg width="20" height="20" viewBox="0 0 24 24" fill="none" stroke="#f7b500" stroke-width="2.2" stroke-linecap="round" stroke-linejoin="round"><path d="M22 16.9v3a2 2 0 0 1-2.2 2 19.8 19.8 0 0 1-8.6-3.1 19.5 19.5 0 0 1-6-6A19.8 19.8 0 0 1 2.1 4.2 2 2 0 0 1 4.1 2h3a2 2 0 0 1 2 1.7c.1.9.4 1.8.7 2.7a2 2 0 0 1-.5 2.1L8 9.8a16 16 0 0 0 6 6l1.3-1.3a2 2 0 0 1 2.1-.4c.9.3 1.8.6 2.7.7a2 2 0 0 1 1.7 2z"/></svg>
    </div>
    <div><small>CALL US:</small><strong>+1 (888) 888 8888</strong></div>
  </div>
</header>

<nav class="band main-nav">
  <a class="current" href="#">HOME</a>
  <a href="#">ABOUT US</a>
  <a href="#">OUR SERVICES</a>
  <a href="#">GALLERY</a>
  <a href="#">LATEST BLOG</a>
  <a href="#">CONTACT US</a>
</nav>

<section class="band hero" role="img" aria-label="Electrician in a hard hat working on an electrical panel">
  <div class="hero-copy">
    <div class="kicker">WELCOME TO</div>
    <h1>FENNICK ELECTRIC</h1>
    <p>Lorem ipsum dolor sit amet, consectetur adipiscing elit sed do eiusmod tempea.</p>
    <a class="btn-solid" href="#">GET STARTED</a>
  </div>
  <div class="slider-dots"><i class="on"></i><i></i><i></i></div>
</section>

<svg class="abs" style="left:0;top:640px" width="1200" height="240" viewBox="0 0 1200 240" aria-hidden="true">
  <path d="M0,30 Q600,296 1200,30 L1200,240 L0,240 Z" fill="#0b4490"/>
  <path d="M0,40 Q600,306 1200,40" fill="none" stroke="#ffffff" stroke-width="8"/>
  <path d="M0,52 Q600,318 1200,52 L1200,240 L0,240 Z" fill="#0b4490"/>
  <circle cx="600" cy="168" r="52" fill="#0b4490" stroke="#ffffff" stroke-width="2"/>
  <circle cx="600" cy="168" r="38" fill="#ffffff"/>
  <circle cx="600" cy="168" r="22" fill="#f7b500"/>
</svg>

<section class="band about">
  <svg class="abs" style="left:100px;top:100px" width="500" height="500" viewBox="0 0 500 500">
    <defs>
      <radialGradient id="aboutWarm" cx=".38" cy=".45" r=".35">
        <stop offset="0" stop-color="#7a5a3e" stop-opacity=".75"/>
        <stop offset="1" stop-color="#7a5a3e" stop-opacity="0"/>
      </radialGradient>
      <radialGradient id="aboutCool" cx=".72" cy=".55" r=".35">
        <stop offset="0" stop-color="#a9bfdc" stop-opacity=".8"/>
        <stop offset="1" stop-color="#a9bfdc" stop-opacity="0"/>
      </radialGradient>
      <linearGradient id="aboutBase" x1="0" y1="0" x2="1" y2="1">
        <stop offset="0" stop-color="#e4e1da"/>
        <stop offset=".5" stop-color="#c9c0b0"/>
        <stop offset="1" stop-color="#d6dae2"/>
      </linearGradient>
    </defs>
    <circle cx="247" cy="239" r="237" fill="#f7b500"/>
    <circle cx="262" cy="241" r="226" fill="#0b4490"/>
    <circle cx="265" cy="241" r="221" fill="#ffffff"/>
    <g role="img" aria-label="Electrician shaking hands with a homeowner in a bright kitchen">
      <circle cx="265" cy="241" r="217" fill="url(#aboutBase)"/>
      <circle cx="265" cy="241" r="217" fill="url(#aboutWarm)"/>
      <circle cx="265" cy="241" r="217" fill="url(#aboutCool)"/>
    </g>
  </svg>
  <div class="about-text">
    <h2 class="section-title"><span class="hl">About</span> Us</h2>
    <p>Lorem ipsum dolor sit amet, consectetur adipiscing elit, sed do eiusmod tempor incididunt ut labore et dolore magna aliqua. Ut enim ad minim veniam, quis nostrud exercitation ullamco laboris nisi ut aliquip ex ea commodo consequat. Duis aute irure dolor in reprehenderit in voluptate velit esse cillum dolore eu fugiat nulla pariatur.</p>
    <p>Excepteur sint occaecat cupidatat non proident, sunt in culpa qui officia deserunt mollit anim id enim ad minim veniam, quis nostrud exercitation est laborum.</p>
    <a class="btn-outline" href="#">LEARN MORE</a>
  </div>
</section>

<section class="band services">
  <h2 class="section-title center-title" style="top:100px"><span class="hl">Our</span> Services</h2>
  <span class="arrow-btn prev"><svg width="12" height="12" viewBox="0 0 12 12"><path d="M8 2 4 6l4 4" fill="none" stroke="#0b4490" stroke-width="2"/></svg></span>
  <article class="service-card" style="left:111px">
    <div class="photo" role="img" aria-label="Lineman in a bucket lift repairing power lines" style="background:radial-gradient(ellipse 70px 60px at 190px 130px,rgba(230,200,120,.8),rgba(230,200,120,0) 70%),radial-gradient(ellipse 120px 60px at 60px 60px,rgba(255,255,255,.8),rgba(255,255,255,0) 70%),linear-gradient(180deg,#6f9fd3 0%,#b8cfe6 55%,#9c8a70 100%)"></div>
    <h3>Site Electrical<br>Experience</h3>
    <p>Lorem ipsum dolor sit amet, consectetur adipiscing elit, sed do eiusmod tempor incididunt ut labore et dolorea.</p>
    <a class="read-more" href="#">READ MORE</a>
  </article>
  <article class="service-card featured" style="left:447px">
    <div class="photo" role="img" aria-label="Technician climbing a power distribution tower" style="background:radial-gradient(ellipse 60px 70px at 140px 130px,rgba(225,140,60,.75),rgba(225,140,60,0) 70%),radial-gradient(ellipse 130px 80px at 200px 40px,rgba(255,255,255,.85),rgba(255,255,255,0) 70%),linear-gradient(180deg,#9fbbdb 0%,#dbe3ec 50%,#8f9aa8 100%)"></div>
    <h3>Power Distribution<br>Experience</h3>
    <p>Lorem ipsum dolor sit amet, consectetur adipiscing elit, sed do eiusmod tempor incididunt ut labore et dolorea.</p>
    <a class="read-more" href="#">READ MORE</a>
  </article>
  <article class="service-card" style="left:784px">
    <div class="photo" role="img" aria-label="Electricians in hard hats inspecting a control panel" style="background:radial-gradient(ellipse 80px 50px at 230px 40px,rgba(240,200,40,.85),rgba(240,200,40,0) 70%),radial-gradient(ellipse 70px 60px at 60px 40px,rgba(240,240,235,.9),rgba(240,240,235,0) 70%),radial-gradient(ellipse 90px 70px at 150px 140px,rgba(180,80,60,.5),rgba(180,80,60,0) 70%),linear-gradient(180deg,#b9bcb6 0%,#8c928d 50%,#4f5550 100%)"></div>
    <h3>Panel<br>Experience</h3>
    <p>Lorem ipsum dolor sit amet, consectetur adipiscing elit, sed do eiusmod tempor incididunt ut labore et dolorea.</p>
    <a class="read-more" href="#">READ MORE</a>
  </article>
  <span class="arrow-btn next"><svg width="12" height="12" viewBox="0 0 12 12"><path d="M4 2l4 4-4 4" fill="none" stroke="#ffffff" stroke-width="2"/></svg></span>
</section>

<section class="band commercial">
  <div class="commercial-text">
    <h2 class="section-title"><span class="hl">Services</span><br>Commercial</h2>
    <p>Lorem ipsum dolor sit amet, consectetur adipiscing elit, sed do eiusmod tempor incididunt ut labore et dolore magna aliqua. Ut enim ad minim veniam, quis nostrud exercitation ullamco laboris nisi ut aliquip ex ea commodo consequat. Duis aute irure dolor in reprehenderit in voluptate velit esse cillum dolore eu fugiat nulla pariatur.</p>
    <a class="btn-outline" href="#" style="margin-top:40px">LEARN MORE</a>
  </div>
  <div class="commercial-photo" role="img" aria-label="Two electricians in safety vests testing wiring in a commercial panel"></div>
</section>

<section class="band gallery">
  <h2 class="section-title center-title" style="top:110px"><span class="hl">Our</span> Gallery</h2>
  <div class="tile" style="left:111px;top:201px;width:480px;height:282px;background:radial-gradient(ellipse 140px 80px at 200px 60px,rgba(245,245,240,.85),rgba(245,245,240,0) 70%),radial-gradient(ellipse 160px 120px at 180px 190px,rgba(235,150,40,.85),rgba(235,150,40,0) 70%),radial-gradient(ellipse 90px 140px at 440px 140px,rgba(190,50,40,.8),rgba(190,50,40,0) 70%),linear-gradient(110deg,#8a6a48 0%,#b08050 40%,#5a4636 75%,#7a3a30 100%)" role="img" aria-label="Two electricians in hard hats reviewing plans"></div>
  <div class="tile" style="left:609px;top:201px;width:480px;height:282px;background:radial-gradient(ellipse 70px 130px at 330px 170px,rgba(50,80,160,.8),rgba(50,80,160,0) 70%),radial-gradient(ellipse 40px 30px at 330px 40px,rgba(240,180,30,.85),rgba(240,180,30,0) 70%),radial-gradient(ellipse 60px 140px at 80px 140px,rgba(60,60,60,.6),rgba(60,60,60,0) 70%),linear-gradient(100deg,#d8dde3 0%,#e6eaee 50%,#c9d3de 100%)" role="img" aria-label="Electrician holding cable beside a wall-mounted panel"></div>
  <div class="tile" style="left:111px;top:500px;width:316px;height:248px;background:radial-gradient(ellipse 120px 60px at 170px 200px,rgba(210,50,40,.85),rgba(210,50,40,0) 70%),radial-gradient(ellipse 90px 70px at 200px 70px,rgba(200,140,100,.8),rgba(200,140,100,0) 70%),linear-gradient(135deg,#e8e6e2 0%,#d6cfc6 50%,#b9a08a 100%)" role="img" aria-label="Hands stripping a wire near a toolbox"></div>
  <div class="tile" style="left:443px;top:500px;width:314px;height:248px;background:radial-gradient(ellipse 70px 90px at 110px 170px,rgba(220,230,40,.85),rgba(220,230,40,0) 70%),radial-gradient(ellipse 60px 40px at 100px 70px,rgba(245,245,245,.85),rgba(245,245,245,0) 70%),radial-gradient(ellipse 80px 120px at 250px 130px,rgba(90,110,100,.7),rgba(90,110,100,0) 70%),linear-gradient(120deg,#b8b09a 0%,#8a8a78 45%,#6a6f60 100%)" role="img" aria-label="Electrician in a safety vest at a server cabinet"></div>
  <div class="tile" style="left:773px;top:500px;width:316px;height:248px;background:radial-gradient(ellipse 70px 100px at 80px 160px,rgba(60,80,120,.8),rgba(60,80,120,0) 70%),radial-gradient(ellipse 90px 30px at 160px 25px,rgba(220,110,50,.8),rgba(220,110,50,0) 70%),linear-gradient(120deg,#a6abb2 0%,#cfd3d8 45%,#bfc5cc 70%,#e2e4e7 100%)" role="img" aria-label="Worker installing overhead conduit"></div>
</section>

<section class="band blog">
  <h2 class="section-title center-title" style="top:70px"><span class="hl">Latest</span> Blog</h2>
  <div class="blog-photo" style="left:111px;top:155px;width:445px;height:283px;background:radial-gradient(ellipse 120px 90px at 250px 200px,rgba(230,120,40,.75),rgba(230,120,40,0) 70%),radial-gradient(ellipse 80px 40px at 250px 110px,rgba(240,190,40,.8),rgba(240,190,40,0) 70%),linear-gradient(180deg,#dfe3e8 0%,#c4ccd4 55%,#7a7c72 100%)" role="img" aria-label="Two workers in hard hats facing a power substation"></div>
  <div class="blog-card">
    <span class="date-pill">10 SEP 2024</span>
    <h4>Lorem ipsum dolor sit amet, con sectetur adipisea</h4>
    <p>Lorem ipsum dolor sit amet, consectetur adipiscing elit, sed do eiusmod tempor ut labore... <a class="read-more" href="#">READ MORE</a></p>
  </div>
  <div class="blog-photo" style="left:573px;top:155px;width:250px;height:195px;background:radial-gradient(ellipse 70px 80px at 70px 120px,rgba(90,150,210,.85),rgba(90,150,210,0) 70%),radial-gradient(ellipse 50px 40px at 190px 110px,rgba(235,190,40,.85),rgba(235,190,40,0) 70%),linear-gradient(120deg,#e9ecef 0%,#d8dee4 50%,#c8ced6 100%)" role="img" aria-label="Electrician testing a breaker with a multimeter"></div>
  <div class="blog-photo" style="left:573px;top:366px;width:250px;height:195px;background:radial-gradient(ellipse 60px 50px at 140px 130px,rgba(230,130,40,.85),rgba(230,130,40,0) 70%),radial-gradient(ellipse 110px 60px at 120px 40px,rgba(245,248,252,.9),rgba(245,248,252,0) 70%),linear-gradient(120deg,#cfdbe8 0%,#e3e9f0 45%,#9aaabb 100%)" role="img" aria-label="Technician in a harness on a transmission tower"></div>
  <div class="blog-item" style="top:183px">
    <span class="date-pill">10 SEP 2024</span>
    <h4>Lorem ipsum dolor sit ame consectetur adipea</h4>
    <p>Lorem ipsum dolor sit amet, consectetur adipiscing elit sed do... <a class="read-more" href="#">READ MORE</a></p>
  </div>
  <div class="blog-item" style="top:395px">
    <span class="date-pill">10 SEP 2024</span>
    <h4>Lorem ipsum dolor sit ame consectetur adipea</h4>
    <p>Lorem ipsum dolor sit amet, consectetur adipiscing elit sed do... <a class="read-more" href="#">READ MORE</a></p>
  </div>
</section>

<footer class="band site-footer">
  <svg class="abs" style="left:0;top:0" width="1200" height="418" viewBox="0 0 1200 418" aria-hidden="true">
    <path d="M0,0 H1200 V40 C880,10 360,-20 0,380 Z" fill="#f3f3f3"/>
    <path d="M1200,40 C880,10 360,-20 0,380" fill="none" stroke="#f7b500" stroke-width="22"/>
  </svg>
  <div class="logo footer-logo"><span class="top">FENNICK</span><span class="bottom">ELECTRIC</span></div>
  <div class="footer-nav">
    <a href="#">HOME</a><span>/</span>
    <a href="#">ABOUT US</a><span>/</span>
    <a href="#">OUR SERVICES</a><span>/</span>
    <a href="#">GALLERY</a><span>/</span>
    <a href="#">LATEST BLOG</a><span>/</span>
    <a href="#">CONTACT US</a>
  </div>
  <div class="footer-contact">
    <span><svg width="12" height="12" viewBox="0 0 24 24" fill="#f7b500"><path d="M22 16.9v3a2 2 0 0 1-2.2 2A19.8 19.8 0 0 1 2.1 4.2 2 2 0 0 1 4.1 2h3a2 2 0 0 1 2 1.7c.1.9.4 1.8.7 2.7a2 2 0 0 1-.5 2.1L8 9.8a16 16 0 0 0 6 6l1.3-1.3a2 2 0 0 1 2.1-.4c.9.3 1.8.6 2.7.7a2 2 0 0 1 1.7 2z"/></svg>+1 (888) 888 8888</span>
    <span>/</span>
    <span><svg width="13" height="11" viewBox="0 0 24 18" fill="#f7b500"><path d="M0 0h24v18H0z"/><path d="M0 0l12 9L24 0" fill="none" stroke="#0b4490" stroke-width="2"/></svg>info@fennickelectric.example</span>
  </div>
  <div class="socials footer-socials" aria-label="Social links">
    <span class="social-dot active"></span>
    <span class="social-dot"></span>
    <span class="social-dot"></span>
    <span class="social-dot"></span>
  </div>
  <div class="footer-rule"></div>
  <div class="copyright">© 2024 FENNICK ELECTRIC &nbsp;|&nbsp; All Rights Reserved</div>
</footer>

</body>
</html>
```